Artist Slasher Horror Film Poster

We need a poster for a presentation that captures the story of the film The Hollow Lantern. The film has not been cast or filmed. The story is about Rupert, a young painter who is tormented by demons to kill his subjects in a creative and gruesome way then pain them in that position as they die. So one of the paintings should be the central image. The background should feature the next subject, Rosalind, a beautiful young woman who is trying to escape being the next painting. One of the situations that could be used are Rupert opening the trunk of a car with her in it or her struggling with him.

Industry/Entity Type

Painting

Other font styles liked:
• Dracula

Requirements
Must have
• Large Painting as the central image.
Nice to have
• Heroine trying to escape painter/killer.
Should not have
• No opinion on this.

```html
<!DOCTYPE html>
<html lang="en">
<head>
<meta charset="utf-8">
<title>The Hollow Lantern — Poster</title>
<link rel="stylesheet" href="https://fonts.googleapis.com/css2?family=Bebas+Neue&family=Oswald:wght@200;300&display=swap">
<style>
  :root {
    --ink: #070607;
    --wall: #1b1a1b;
    --wall-light: #4a4846;
    --frame: #120f0e;
    --gilt: #b59a6a;
    --canvas-red: #c7452f;
    --canvas-hot: #e07a4a;
    --canvas-deep: #5c1618;
    --blood: #a0141a;
    --blood-dark: #4e0709;
    --silver-top: #f2f2f2;
    --silver-bottom: #5d5d5d;
  }
  * { margin: 0; padding: 0; box-sizing: border-box; }
  html, body { width: 776px; height: 1200px; overflow: hidden; background: var(--ink); }
  .poster {
    position: relative;
    width: 776px;
    height: 1200px;
    overflow: hidden;
    background:
      radial-gradient(ellipse 260px 200px at 390px 760px, rgba(110,106,100,.55), transparent 70%),
      radial-gradient(ellipse 300px 260px at 390px 140px, rgba(90,88,84,.5), transparent 70%),
      radial-gradient(ellipse 360px 480px at 390px 450px, rgba(60,58,56,.6), transparent 75%),
      linear-gradient(180deg, var(--wall) 0%, #0d0c0d 70%, var(--ink) 100%);
  }
  .floor {
    position: absolute;
    left: 0; right: 0; bottom: 0;
    height: 90px;
    background:
      repeating-linear-gradient(90deg, rgba(255,255,255,.03) 0 2px, transparent 2px 96px),
      linear-gradient(180deg, #0a0909 0%, #1c1a19 100%);
  }
  .frame {
    position: absolute;
    left: 176px; top: 150px;
    width: 434px; height: 540px;
    background: var(--frame);
    border-radius: 18px;
    box-shadow: 0 20px 40px rgba(0,0,0,.8), inset 0 0 30px rgba(181,154,106,.15);
  }
  .frame__stud {
    position: absolute;
    width: 22px; height: 22px;
    border-radius: 50%;
    background: radial-gradient(circle at 40% 35%, #d9c7a3, #6e5c44);
  }
  .frame__stud--tl { left: 26px; top: 24px; }
  .frame__stud--tr { right: 26px; top: 24px; }
  .frame__stud--bl { left: 20px; bottom: 34px; }
  .frame__stud--br { right: 20px; bottom: 34px; }
  .frame__mat {
    position: absolute;
    left: 74px; top: 80px;
    width: 282px; height: 368px;
    border: 3px solid var(--gilt);
    background: #0c0a0a;
    padding: 9px;
  }
  .painting {
    width: 100%; height: 100%;
    background:
      radial-gradient(ellipse 90px 140px at 55% 35%, var(--canvas-hot), transparent 70%),
      radial-gradient(ellipse 150px 200px at 45% 50%, var(--canvas-red), transparent 80%),
      linear-gradient(180deg, var(--canvas-deep) 0%, #a8322a 40%, #3a0c16 100%);
  }
  .drips {
    position: absolute;
    left: 300px; top: 676px;
    width: 180px; height: 120px;
    background: linear-gradient(180deg, var(--blood) 0%, rgba(160,20,26,.5) 50%, transparent 100%);
    -webkit-mask: repeating-linear-gradient(90deg, #000 0 10px, transparent 10px 36px);
            mask: repeating-linear-gradient(90deg, #000 0 10px, transparent 10px 36px);
  }
  .title {
    position: absolute;
    left: 50px; right: 50px; top: 818px;
    display: flex;
    justify-content: center;
    align-items: flex-end;
    gap: 10px;
    white-space: nowrap;
  }
  .title__lead {
    display: flex;
    flex-direction: column;
    font-family: "Oswald", sans-serif;
    font-weight: 200;
    font-size: 58px;
    line-height: 1;
    letter-spacing: -1px;
    text-transform: uppercase;
    background: linear-gradient(180deg, var(--silver-top), var(--silver-bottom));
    -webkit-background-clip: text;
            background-clip: text;
    color: transparent;
    padding-bottom: 6px;
  }
  .title__lead span:first-child { align-self: flex-end; }
  .title__main {
    font-family: "Bebas Neue", sans-serif;
    font-size: 158px;
    line-height: .82;
    letter-spacing: 1px;
    text-transform: uppercase;
    background: linear-gradient(180deg, #d21a20 0%, var(--blood) 55%, var(--blood-dark) 100%);
    -webkit-background-clip: text;
            background-clip: text;
    color: transparent;
    filter: drop-shadow(0 8px 10px rgba(0,0,0,.85));
  }
</style>
</head>
<body>
  <main class="poster">
    <div class="floor"></div>

    <div class="frame">
      <span class="frame__stud frame__stud--tl"></span>
      <span class="frame__stud frame__stud--tr"></span>
      <span class="frame__stud frame__stud--bl"></span>
      <span class="frame__stud frame__stud--br"></span>
      <div class="frame__mat">
        <div class="painting" role="img" aria-label="Blurred red painting of a victim's hands pressed against the canvas"></div>
      </div>
    </div>

    <div class="drips" role="img" aria-label="Blood dripping from the bottom of the frame"></div>

    <h1 class="title">
      <span class="title__lead"><span>The</span><span>Hollow</span></span>
      <span class="title__main">Lantern</span>
    </h1>
  </main>
</body>
</html>
```